Stationary Set Rebrand for Brennick

We are a Canadian Distribution and Service Company that was established in 1969. Over the past 5 decades we have expanded our business and have warehouses across Canada. We specialize in adhesive tapes, adhesives, films, safety, warehouse, shipping, janitorial and packaging supplies.

We have updated our logo design and would like a new corporate branding identity that includes a new fresh Stationary Set (Business Cards, Letterhead, Letterhead MS Word, Envelope, Presentation Folders, Email Signatures, Notepad Covers, etc.)

Target Market(s)

Industrial Business Sector

Font styles to use
Sans Serif

Colors
0054AA
0677BA
7BADD7
CADEEF
E8F1F8
0094D4
00A9DD
6FCCEA
C7EBF8
E9F6FB
00AB8E
00BBA5
67D7C9
C6EFE9
E9F9F6
EB3D1F
EC4F4E
F09395
F8D3D4
FCEDEE

Requirements
Should not have
• Colors not too light, darker colours preferred

```html
<!DOCTYPE html>
<html lang="en">
<head>
<meta charset="UTF-8">
<title>Brennick Business Card</title>
<link rel="stylesheet" href="https://fonts.googleapis.com/css2?family=Montserrat:wght@400;500;700;800&display=swap">
<style>
  :root {
    --stage: #3b3b3d;
    --card: #19191a;
    --brand-red: #d81f2a;
    --white: #ffffff;
    --text-soft: #f2f2f2;
    --gloss-light: #cfcfcf;
    --gloss-mid: #5a5a5b;
    --gloss-dark: #202021;
  }
  * { box-sizing: border-box; margin: 0; padding: 0; }
  html, body {
    width: 1200px; height: 689px; overflow: hidden;
    background: var(--stage);
    font-family: "Montserrat", Arial, sans-serif;
  }
  .stage { position: relative; width: 1200px; height: 689px; }
  .card {
    position: absolute; top: 190px;
    width: 540px; height: 309px;
    background: var(--card);
    border-radius: 22px;
    box-shadow: 0 18px 40px rgba(0,0,0,.45);
    overflow: hidden;
  }
  .card--back { left: 40px; }
  .card--front { left: 620px; }

  .back-emblem {
    position: absolute; left: 175px; top: 60px;
    width: 190px; height: 190px;
    border-radius: 50%;
    background: linear-gradient(100deg, var(--gloss-light) 0%, var(--gloss-mid) 45%, var(--gloss-dark) 75%);
  }

  .front-emblem {
    position: absolute; left: 300px; top: 40px;
    width: 220px; height: 220px;
    border-radius: 50%;
    background: var(--brand-red);
  }

  .brand-name {
    position: absolute; left: 32px; top: 40px;
    font-weight: 800; font-size: 46px; letter-spacing: -1px;
    color: var(--white); line-height: 1;
  }

  .person {
    position: absolute; left: 32px; top: 112px;
    padding-left: 16px;
    border-left: 8px solid var(--brand-red);
  }
  .person__name {
    font-weight: 700; font-size: 25px; color: var(--brand-red); line-height: 1.1;
  }
  .person__title {
    font-weight: 500; font-size: 14px; color: var(--text-soft); margin-top: 4px;
  }

  .address {
    position: absolute; left: 56px; top: 184px;
    font-size: 13px; color: var(--text-soft); line-height: 1.45;
  }

  .contacts {
    position: absolute; left: 56px; top: 228px;
    list-style: none;
    font-size: 12.5px; color: var(--text-soft); line-height: 1.55;
  }
  .contacts li { display: flex; align-items: center; gap: 8px; }
  .contacts svg { width: 12px; height: 12px; fill: var(--brand-red); flex: none; }
</style>
</head>
<body>
<main class="stage">
  <section class="card card--back" aria-label="Card back">
    <div class="back-emblem" role="img" aria-label="Glossy spot-varnish brand emblem"></div>
  </section>

  <section class="card card--front" aria-label="Card front">
    <div class="front-emblem" role="img" aria-label="Large red brand emblem"></div>

    <div class="brand-name">Brennick</div>

    <div class="person">
      <p class="person__name">Daniel Harker</p>
      <p class="person__title">Managing Director</p>
    </div>

    <p class="address">Your address, City<br>State, Zip 1234</p>

    <ul class="contacts">
      <li>
        <svg viewBox="0 0 24 24" aria-hidden="true"><path d="M6.6 10.8a15.1 15.1 0 0 0 6.6 6.6l2.2-2.2c.3-.3.7-.4 1-.2 1.1.4 2.3.6 3.6.6.6 0 1 .4 1 1V20c0 .6-.4 1-1 1A17 17 0 0 1 3 4c0-.6.4-1 1-1h3.5c.6 0 1 .4 1 1 0 1.3.2 2.5.6 3.6.1.3 0 .7-.2 1z"/></svg>
        123 456 789
      </li>
      <li>
        <svg viewBox="0 0 24 24" aria-hidden="true"><path d="M2 5h20v14H2z M2 5l10 8 10-8" stroke="#19191a" stroke-width="1.6"/></svg>
        info@brennickmail.com
      </li>
      <li>
        <svg viewBox="0 0 24 24" aria-hidden="true"><circle cx="12" cy="12" r="10"/><path d="M2 12h20M12 2c3 3 3 17 0 20M12 2c-3 3-3 17 0 20" stroke="#19191a" stroke-width="1.4" fill="none"/></svg>
        www.brennickwebsite.com
      </li>
    </ul>
  </section>
</main>
</body>
</html>
```